Business Card for brovaLINK

Create a Business Card with an existing logo for brovaLINK AG. We are a Information Technology company that does consulting and developing SW to automate business processes. The main colors are given from the logo.

Industry/Entity Type

Business

Requirements
Nice to have
• we use a a font style Century Gothic in our documents

```html
<!DOCTYPE html>
<html lang="en">
<head>
<meta charset="utf-8">
<title>brovaLINK AG – Business Card</title>
<link href="https://fonts.googleapis.com/css2?family=Questrial&display=swap" rel="stylesheet">
<style>
  :root {
    --backdrop: #e4e4e2;
    --card: #f6f6f6;
    --ink: #3f3f42;
    --ink-soft: #6b6b70;
    --brand-blue: #2f86d1;
    --brand-green: #3aa935;
    --band-dark: #232326;
    --orb: #e9e9ea;
  }
  * { margin: 0; padding: 0; box-sizing: border-box; }
  html, body {
    width: 1200px; height: 900px; overflow: hidden;
    background: var(--backdrop);
    font-family: "Questrial", "Century Gothic", sans-serif;
    color: var(--ink);
  }
  .canvas { position: relative; width: 1200px; height: 900px; }
  .card {
    position: absolute; left: 320px;
    width: 560px; height: 320px;
    background: var(--card);
    overflow: hidden;
    box-shadow: 0 6px 18px rgba(0,0,0,.12);
  }
  .card--front { top: 110px; }
  .card--back { top: 470px; }

  .wordmark {
    position: absolute; display: flex; align-items: center; gap: 10px;
    font-size: 30px; color: var(--ink-soft); letter-spacing: .5px;
  }
  .wordmark__dot {
    width: 26px; height: 26px; border-radius: 50%;
    background: var(--brand-blue);
  }
  .card--front .wordmark { left: 150px; top: 72px; }
  .card--back .wordmark { left: 150px; top: 40px; }

  .front-orb { position: absolute; right: 0; bottom: 0; }

  .holder { position: absolute; left: 150px; top: 108px; }
  .holder__name {
    font-size: 11px; letter-spacing: 3px; text-transform: uppercase;
    color: var(--ink-soft);
  }
  .holder__role {
    margin-top: 3px; font-size: 11px; letter-spacing: 3px;
    color: var(--brand-green);
  }

  .contact {
    position: absolute; left: 235px; top: 150px;
    list-style: none;
  }
  .contact__item {
    display: flex; align-items: center; gap: 12px;
    height: 20px; font-size: 12.5px; letter-spacing: 2px; color: var(--ink);
  }
  .contact__icon { width: 12px; height: 12px; flex: none; }

  .edge-bands { position: absolute; left: 0; bottom: 0; }
</style>
</head>
<body>
<main class="canvas">

  <section class="card card--front" aria-label="Business card front">
    <div class="wordmark"><span class="wordmark__dot"></span><span>brovaLINK</span></div>
    <svg class="front-orb" width="200" height="170" viewBox="0 0 200 170" aria-hidden="true">
      <circle cx="140" cy="150" r="105" fill="var(--orb)"/>
    </svg>
  </section>

  <section class="card card--back" aria-label="Business card back">
    <div class="wordmark"><span class="wordmark__dot"></span><span>brovaLINK</span></div>

    <div class="holder">
      <p class="holder__name">Lukas Weber</p>
      <p class="holder__role">CEO</p>
    </div>

    <ul class="contact">
      <li class="contact__item">
        <svg class="contact__icon" viewBox="0 0 12 12" aria-hidden="true"><path d="M6 0.5a4 4 0 0 0-4 4c0 3 4 7 4 7s4-4 4-7a4 4 0 0 0-4-4z" fill="var(--brand-blue)"/><circle cx="6" cy="4.5" r="1.4" fill="var(--card)"/></svg>
        Talweg 12, 5400 Baden, Switzerland
      </li>
      <li class="contact__item">
        <svg class="contact__icon" viewBox="0 0 12 12" aria-hidden="true"><path d="M2.5 1h2l1 3-1.5 1a7 7 0 0 0 3 3l1-1.5 3 1v2a1.5 1.5 0 0 1-1.5 1.5A9.5 9.5 0 0 1 1 2.5 1.5 1.5 0 0 1 2.5 1z" fill="var(--brand-blue)"/></svg>
        +41 56 210 48 36
      </li>
      <li class="contact__item">
        <svg class="contact__icon" viewBox="0 0 12 12" aria-hidden="true"><rect x="3" y="0.5" width="6" height="11" rx="1.2" fill="var(--brand-blue)"/><rect x="4" y="1.8" width="4" height="7" fill="var(--card)"/></svg>
        +41 79 455 62 19
      </li>
      <li class="contact__item">
        <svg class="contact__icon" viewBox="0 0 12 12" aria-hidden="true"><rect x="0.5" y="2" width="11" height="8" rx="1" fill="var(--brand-blue)"/><path d="M1 2.8l5 3.6 5-3.6" stroke="var(--card)" stroke-width="1" fill="none"/></svg>
        lukas.weber@brovalink.ch
      </li>
      <li class="contact__item">
        <svg class="contact__icon" viewBox="0 0 12 12" aria-hidden="true"><circle cx="6" cy="6" r="5.5" fill="var(--brand-blue)"/><path d="M0.8 6h10.4M6 0.8c-2.2 2.8-2.2 7.6 0 10.4M6 0.8c2.2 2.8 2.2 7.6 0 10.4" stroke="var(--card)" stroke-width=".8" fill="none"/></svg>
        www.brovalink.ch
      </li>
    </ul>

    <svg class="edge-bands" width="560" height="40" viewBox="0 0 560 40" aria-hidden="true">
      <rect x="0" y="28" width="190" height="12" fill="var(--brand-blue)"/>
      <path d="M175 40 C185 40 188 20 205 20 L560 20 L560 40 Z" fill="var(--band-dark)"/>
    </svg>
  </section>

</main>
</body>
</html>
```